Open Harbor book needs a cover design

I need a front and back cover design that demonstrates a strong sense of possibility that trust can be repaired even if things look bleak. Repairing trust is difficult, but this book is full of wisdom, proven strategies, and doctoral research to help people strengthen relationships and improve trust. It can help any group: business, nonprofit, education, service. Showing diversity of groups and people is very important. For the cover title, there should be a play on words: "Open Harbor: Is it? Within Reach" should have the words "is it?" crossed out and the words "It IS! should be replaced there in a striking way. Perhaps in red ink. For publishing purposes, book will be titled Open Harbor: It IS Within Reach! Please see the attachment for an example. The book layout is approximately 260 pages.

A business self-help book, but the target is any person in a group that feels they have lost trust in each other. It can be just a normal person struggling in a volunteer group they are a part of, or a supervisor whose group is not working well together. It can be a leader who just wants their group to be stronger.

Business Management

• Allise - I believe is being used on the interior of the book for the title page and headings

• Show hope and possibility in the midst of difficulty. Must have a play on the words in the title "Open Harbor: Is it? Within Reach" with crossing out "is it?" with "It IS!" (see attached example) Must include the author's name: Marla Quentin, PhD Must include a smaller tagline: "Practical Steps to Move Teams Forward Again"
• Showing diverse people, or hands. Diverse kinds of groups - not just business. A colorful cover. Maybe show the complexity of trust when it is broken...broken pieces of trust that are then picked up and put together when people work together. Could show people (or images of hands) or other ways to show that it's a choice and it is possible to repair broken trust. I'd also like to convey a sense of a group - not just random people. That they have something at stake to work on repairing trust together and this book can help them.
• If images of people are used, just showing one gender or race is not okay. Nor just binary choices: like an image containing one man and one woman, or one white person and one person of color - otherwise it seems that the book on Open Harbor is about race or gender relations.

```html
<!DOCTYPE html>
<html lang="en">
<head>
<meta charset="utf-8">
<title>Open Harbor — Book Cover</title>
<link rel="stylesheet" href="https://fonts.googleapis.com/css2?family=Fresca&family=Crimson+Pro:wght@500&display=swap">
<style>
  :root {
    --backdrop-center: #e6f3fb;
    --backdrop-edge: #cfe6f4;
    --cover-white: #ffffff;
    --ink-dark: #3f3a3b;
    --ink-red: #e3000f;
    --art-top: #fbfbfc;
    --art-mid: #e9e6ea;
    --art-accent: #f3dfe1;
  }
  * { margin: 0; padding: 0; box-sizing: border-box; }
  html, body {
    width: 1200px;
    height: 1200px;
    overflow: hidden;
  }
  body {
    background: radial-gradient(circle at 50% 50%, var(--backdrop-center) 0%, var(--backdrop-edge) 100%);
    position: relative;
  }
  .book-cover {
    position: absolute;
    left: 230px;
    top: 47px;
    width: 740px;
    height: 1110px;
    background: var(--cover-white);
  }
  .cover-art {
    position: absolute;
    left: 60px;
    top: 0;
    width: 640px;
    height: 330px;
    display: block;
  }
  .title-main {
    position: absolute;
    left: 0;
    width: 100%;
    top: 440px;
    text-align: center;
    font-family: "Fresca", sans-serif;
    font-size: 138px;
    line-height: 1;
    color: var(--ink-dark);
    letter-spacing: -1px;
  }
  .title-main .title-accent { color: var(--ink-red); }
  .title-question {
    position: absolute;
    left: 0;
    width: 100%;
    top: 628px;
    text-align: center;
    font-family: "Fresca", sans-serif;
    font-size: 50px;
    line-height: 1;
    color: var(--ink-dark);
  }
  .title-question .struck {
    position: relative;
    display: inline-block;
    margin-left: -30px;
  }
  .title-question .struck::after {
    content: "";
    position: absolute;
    left: -4px;
    right: -4px;
    top: 52%;
    height: 3px;
    background: var(--ink-red);
  }
  .title-answer {
    position: absolute;
    left: 0;
    width: 100%;
    top: 668px;
    text-align: center;
    font-family: "Fresca", sans-serif;
    font-size: 98px;
    line-height: 1;
    color: var(--ink-dark);
  }
  .tagline {
    position: absolute;
    left: 0;
    width: 100%;
    top: 824px;
    text-align: center;
    font-family: "Fresca", sans-serif;
    font-size: 32px;
    line-height: 34px;
    color: var(--ink-dark);
  }
  .author {
    position: absolute;
    left: 0;
    width: 100%;
    top: 1008px;
    text-align: center;
    font-family: "Crimson Pro", serif;
    font-weight: 500;
    font-size: 40px;
    line-height: 1;
    color: var(--ink-dark);
  }
</style>
</head>
<body>
  <main class="book-cover">
    <svg class="cover-art" viewBox="0 0 640 330" role="img" aria-label="Illustration of a Newton's cradle: four silver spheres hanging at rest and one red sphere swinging out to the right">
      <defs>
        <linearGradient id="art-fill" x1="0" y1="0" x2="1" y2="1">
          <stop offset="0%" stop-color="var(--art-top)"/>
          <stop offset="60%" stop-color="var(--art-mid)"/>
          <stop offset="100%" stop-color="var(--art-accent)"/>
        </linearGradient>
      </defs>
      <rect width="640" height="330" fill="url(#art-fill)"/>
    </svg>

    <h1 class="title-main">Open <span class="title-accent">Harbor</span></h1>
    <p class="title-question"><span class="struck">Is it?</span></p>
    <p class="title-answer">Within Reach</p>

    <p class="tagline">Practical Steps<br>to Move Teams Forward Again</p>

    <p class="author">Marla Quentin, PhD</p>
  </main>
</body>
</html>
```